ULMIRA card Technical Architecture

Hello everyone ULMIRA: It is a consulting firm in Architecture and Construction. I require a card duplexing, sober, elegant, classic but not boring. Update 1: Use the following data for the card. Name: Gonzalo Pereda Mauricio Villalta Position: COO Twitter: @ulmiraAT Homepage: ulmira-example.com home address not include the participation of all thank you.

Target Market(s)

Construction companies, Architects and Consulting Engineers

Industry/Entity Type

Consulting

Contact Information for Business Card

Los campos que debe tener:
Nombre, Cargo, email, homepage y twitter

Font styles to use
Serif
Sans Serif
Other font styles liked:
• Me gustan playfair display, open sans y roboto, pero estoy sujeto a sus propuestas

Requirements
Must have
• Colors: Present combined proposals in white, red, gray and black Update 1: The two names must be clearly differentiated from the two surnames
Nice to have
• They are free to present their best proposals. I will bring them immediate feedback to the extent you can go see their designs. Complete data for card and logo files will give the winner the

```html
<!DOCTYPE html>
<html lang="es">
<head>
<meta charset="utf-8">
<title>ULMIRA — Tarjeta de presentación</title>
<link rel="stylesheet" href="https://fonts.googleapis.com/css2?family=Open+Sans:wght@400;600;700&display=swap">
<style>
  :root {
    --page: #ffffff;
    --card: #000000;
    --red: #c8102e;
    --red-bright: #ef4a6c;
    --white: #ffffff;
    --divider: #2a2a2a;
  }
  * { margin: 0; padding: 0; box-sizing: border-box; }
  html, body {
    width: 1200px; height: 900px; overflow: hidden;
    background: var(--page);
    font-family: "Open Sans", Arial, sans-serif;
  }
  .card {
    position: absolute;
    top: 271px;
    width: 457px; height: 281px;
    background: var(--card);
    border-radius: 14px;
    overflow: hidden;
  }
  .card--front { left: 137px; }
  .card--back { left: 626px; }

  /* front */
  .front-brand {
    position: absolute; left: 0; top: 0;
    width: 232px; height: 281px;
    display: flex; align-items: center; justify-content: center;
    color: var(--red-bright);
    font-weight: 700; font-size: 30px; letter-spacing: 2px;
  }
  .front-divider {
    position: absolute; left: 232px; top: 64px;
    width: 1px; height: 152px;
    background: linear-gradient(to bottom, transparent, var(--divider) 20%, var(--divider) 80%, transparent);
  }
  .contact-block {
    position: absolute; left: 257px; top: 72px;
    color: var(--white);
  }
  .person-name {
    color: var(--red-bright);
    font-weight: 700; font-size: 14.5px; line-height: 19px;
  }
  .person-role {
    font-size: 12px; line-height: 18px; margin-top: 1px;
  }
  .contact-list { list-style: none; margin-top: 19px; font-size: 12px; }
  .contact-list li {
    display: flex; align-items: center; gap: 7px; height: 16px;
  }
  .contact-list li.contact-social { margin-top: 12px; }
  .contact-icon { width: 9px; height: 9px; flex: none; }

  /* back */
  .back-mark {
    position: absolute; left: 216px; top: 78px;
    width: 22px; height: 22px; background: var(--red);
  }
  .back-name {
    position: absolute; left: 0; right: 0; top: 150px;
    text-align: center; color: var(--white);
    font-weight: 400; font-size: 38px; line-height: 40px;
    letter-spacing: 12px; padding-left: 12px;
  }
  .back-rule {
    position: absolute; left: 88px; width: 282px; top: 192px;
    height: 1px; background: #5a0a14;
  }
  .back-tagline {
    position: absolute; left: 0; right: 0; top: 197px;
    text-align: center; color: var(--red);
    font-size: 10.5px; letter-spacing: 3.6px; text-transform: uppercase;
  }
</style>
</head>
<body>
  <section class="card card--front" aria-label="Frente de la tarjeta">
    <div class="front-brand">ULMIRA</div>
    <div class="front-divider"></div>
    <div class="contact-block">
      <p class="person-name">Mauricio Gonzalo<br>Pereda Villalta</p>
      <p class="person-role">Director of Operations</p>
      <ul class="contact-list">
        <li>
          <svg class="contact-icon" viewBox="0 0 9 9" aria-hidden="true"><rect x="2" y="0.5" width="5" height="8" rx="1" fill="none" stroke="#ef4a6c" stroke-width="1.2"/></svg>
          (+571) 555 010 0000
        </li>
        <li>
          <svg class="contact-icon" viewBox="0 0 9 9" aria-hidden="true"><circle cx="4.5" cy="4.5" r="4" fill="#ef4a6c"/></svg>
          www.ulmira-example.com
        </li>
        <li class="contact-social">
          <svg class="contact-icon" viewBox="0 0 9 9" aria-hidden="true"><rect x="0" y="0" width="9" height="9" rx="1.5" fill="#ef4a6c"/></svg>
          @ulmiraAT
        </li>
      </ul>
    </div>
  </section>

  <section class="card card--back" aria-label="Reverso de la tarjeta">
    <div class="back-mark"></div>
    <div class="back-name">ULMIRA</div>
    <div class="back-rule"></div>
    <div class="back-tagline">Arquitectura Técnica</div>
  </section>
</body>
</html>
```